I have written a book called "Whispers from the Back Office - Uncover the trade tricks advisers bill huge fees every season for and would rather keep hidden"

This book will be sold through this webpage as an ebook. i have attached a copy of the cover of the book and I would like the website to be consistent with the look and feel of the book cover.

Target Market(s)

Business owners

Industry/Entity Type

Business

Requirements
Must have
• There has been a video produced for the promotion of this book which is yet to be completed. The video will be on ClipNest and the video needs to be prominent on the homepage.

I need to be able to manage and change the content as I wish on the website eg wordpress.

The page will need have a Coinvey purchase button

Also a 100% money back guarantee sign

Nice to have
• Friendloop plug in to show how many people like the page

Should not have
• I don't want the homepage or any of the other pages to be too cluttered

```html
<!DOCTYPE html>
<html lang="en">
<head>
<meta charset="utf-8">
<title>Whispers from the Back Office</title>
<link href="https://fonts.googleapis.com/css2?family=Oswald:wght@300;400;500&family=Open+Sans:wght@400;600;700&display=swap" rel="stylesheet">
<style>
:root{
  --brand:#0aa6e6;
  --brand-dark:#0b86c4;
  --ink:#222;
  --grey:#666;
  --grey-light:#8a8a8a;
  --rule:#dcdcdc;
  --panel:#f1f1f1;
  --footer:#3b3b3b;
  --white:#fff;
}
*{margin:0;padding:0;box-sizing:border-box}
html,body{width:986px;height:1200px;overflow:hidden;background:var(--white)}
body{position:relative;font-family:"Open Sans",Arial,sans-serif;color:var(--grey)}
.abs{position:absolute}
.topline{left:0;top:0;width:986px;height:5px;background:var(--brand)}
.logo{left:98px;top:26px;font-family:"Oswald",sans-serif;line-height:1}
.logo .l1{display:block;color:var(--brand);font-size:35px;font-weight:400;letter-spacing:-.5px}
.logo .l2{display:block;color:#111;font-size:26px;font-weight:400;margin-top:5px;letter-spacing:-.3px}
.nav{right:106px;top:47px;display:flex;gap:33px;font-family:"Oswald",sans-serif;font-weight:300;font-size:13.5px;color:#555;text-transform:uppercase}
.hero{left:0;top:114px;width:986px;height:354px;background:var(--brand)}
.hero-title{left:107px;top:180px;font-family:"Oswald",sans-serif;font-weight:400;color:var(--white);font-size:37px;line-height:36px;text-transform:uppercase;letter-spacing:-.5px}
.hero-text{left:107px;top:276px;width:392px;font-family:"Oswald",sans-serif;font-weight:300;color:var(--white);font-size:12.4px;line-height:18px;text-transform:uppercase}
.btn-light{left:107px;top:366px;width:100px;height:37px;border-radius:7px;background:linear-gradient(#fff,#d6d6d6);border:1px solid #c8c8c8;box-shadow:0 1px 3px rgba(0,0,0,.25);font-family:"Oswald",sans-serif;font-weight:300;font-size:16px;color:#777;display:flex;align-items:center;justify-content:center}
.dots{left:107px;top:438px;display:flex;gap:4px}
.dots span{width:8px;height:8px;border-radius:50%;background:#9aa3a8;box-shadow:inset 0 1px 1px rgba(0,0,0,.4)}
.dots span.on{background:#444}
.hero-art{left:535px;top:120px;width:310px;height:348px;border-radius:4px;background:linear-gradient(135deg,#f4f4f4 0%,#e2e2e2 45%,#2a2a2a 75%,#111 100%);opacity:.9}
.intro-title{left:0;width:986px;top:480px;text-align:center;font-family:"Oswald",sans-serif;font-weight:400;color:var(--brand);font-size:29px}
.intro-sub{left:0;width:986px;top:524px;text-align:center;font-family:"Oswald",sans-serif;font-weight:300;color:#555;font-size:13.6px;text-transform:uppercase;letter-spacing:-.2px}
.rule{left:107px;top:550px;width:773px;height:1px;background:var(--rule)}
.feature{top:565px;width:250px;text-align:center}
.feature .pic{margin:0 auto;width:100px;height:100px;border-radius:6px}
.feature h3{margin-top:17px;font-family:"Oswald",sans-serif;font-weight:300;font-size:16px;line-height:19px;color:#444;text-transform:uppercase}
.feature p{margin-top:9px;font-size:8.3px;line-height:14.6px;color:#666}
.btn-blue{display:inline-block;margin-top:14px;width:88px;height:26px;line-height:26px;border-radius:3px;background:linear-gradient(#1cb2ef,#0b82c2);border:1px solid #0a74ad;color:var(--white);font-family:"Oswald",sans-serif;font-weight:300;font-size:10.5px;text-transform:uppercase}
.f1{left:90px}.f2{left:367px}.f3{left:641px;top:557px}
.pic-dice{background:linear-gradient(135deg,#c0202a,#e9e9e9)}
.pic-cash{background:linear-gradient(180deg,#d9dfd3,#5d8a4a)}
.pic-badge{width:130px!important;border-radius:50%!important;background:radial-gradient(circle,#f2b72a 0%,#e39a14 60%,#c02a22 100%)}
.rule2{left:98px;top:840px;width:790px;height:3px;border-top:1px solid var(--rule);border-bottom:1px solid var(--rule)}
.welcome{left:98px;top:864px;font-family:"Oswald",sans-serif;font-weight:400;font-size:16.5px;color:#222;text-transform:uppercase;letter-spacing:-.3px}
.video{left:98px;top:899px;width:247px;height:203px;background:linear-gradient(90deg,#6a5246 0%,#cfc9c4 45%,#e6e6e6 60%,#2d9ad8 100%)}
.video svg{position:absolute;left:82px;top:82px}
.body-copy{left:353px;top:897px;width:264px;font-family:Arial,sans-serif;font-size:10.1px;line-height:13.2px;color:#777;text-align:justify}
.body-copy p+p{margin-top:13px}
.side{left:640px;width:247px;border:1px solid var(--rule);background:var(--panel)}
.side-guarantee{top:867px;height:58px}
.side-guarantee .seal{position:absolute;left:14px;top:8px;width:50px;height:42px;border-radius:50%;background:radial-gradient(circle,#f2b72a 0%,#e39a14 60%,#c02a22 100%)}
.side-guarantee .label{position:absolute;left:88px;top:16px;font-family:"Oswald",sans-serif;font-weight:300;color:#777;font-size:17px;text-transform:uppercase}
.side-buy{top:929px;height:58px}
.buy-btn{position:absolute;left:8px;top:12px;width:153px;height:34px;border-radius:17px;background:linear-gradient(#ffe27a,#f5a623);border:1px solid #d88d1c;color:#213a7d;font-family:"Open Sans",sans-serif;font-weight:700;font-size:17px;display:flex;align-items:center;justify-content:center}
.cards{position:absolute;left:167px;top:8px;display:grid;grid-template-columns:36px 36px;gap:4px}
.cards span{height:19px;background:var(--white);border:1px solid #ccc;font-size:6.5px;font-weight:600;color:#333;display:flex;align-items:center;justify-content:center}
.side-social{top:991px;height:110px;background:var(--white)}
.social-head{position:absolute;left:6px;top:5px;display:flex;gap:7px;align-items:flex-start}
.social-head .sq{width:24px;height:24px;background:#3b5a98}
.social-head b{display:block;font-size:10px;color:#3b5a98;font-weight:700}
.like{display:inline-block;margin-top:3px;font-size:7px;padding:2px 5px;border:1px solid #bbb;background:#f4f4f4;color:#333}
.social-count{position:absolute;left:5px;top:45px;width:237px;border-top:1px solid var(--rule);padding-top:4px;font-size:7.5px;color:#333;font-weight:600}
.fans{position:absolute;left:5px;top:60px;display:flex;gap:4px}
.fan{width:36px;text-align:center;font-size:6px;color:#777}
.fan i{display:block;height:36px;background:linear-gradient(#8c8c8c,#3a3a3a);margin-bottom:3px}
.footer{left:0;top:1139px;width:986px;height:61px;background:var(--footer)}
.copyright{left:99px;top:1160px;font-family:Arial,sans-serif;font-size:10.2px;color:#eee}
.copyright span{margin:0 6px;color:#aaa}
.social-links{right:106px;top:1157px;display:flex;gap:7px}
.social-links span{font-size:8.5px;color:#eee;display:flex;align-items:center;gap:3px}
.social-links span i{width:8px;height:8px;background:#3a8fd9;display:inline-block}
</style>
</head>
<body>
<div class="abs topline"></div>

<header>
  <div class="abs logo"><span class="l1">WHISPERS FROM</span><span class="l2">THE BACK OFFICE</span></div>
  <nav class="abs nav"><span>Home</span><span>About Us</span><span>Online Sale</span><span>Buy Now</span><span>Contact</span></nav>
</header>

<section class="abs hero"></section>
<h1 class="abs hero-title">Whispers from<br>the Back Office</h1>
<p class="abs hero-text">Sed ut perspiciatis unde omnis iste natus error sit voluptatem accusantium doloremque laudantium, totam rem aperiam, eaque ipsa quae ab illo inventore veritatis et quasi architecto beatae vitae dicta sunt explicabo. Nemo enim</p>
<div class="abs btn-light">LEARN MORE</div>
<div class="abs dots"><span></span><span class="on"></span><span></span></div>
<div class="abs hero-art" role="img" aria-label="Book cover artwork: paper speech banner with the book title beside a businessman silhouette"></div>

<h2 class="abs intro-title">We create for Accounting</h2>
<p class="abs intro-sub">Uncover the trade tricks advisers bill huge fees every season for and would rather keep hidden</p>
<div class="abs rule"></div>

<div class="abs feature f1">
  <div class="pic pic-dice" role="img" aria-label="Illustration of red dice and a figure"></div>
  <h3>Uncover the trade<br>tricks advisers</h3>
  <p>Lorem Ipsum is simply dummy text of the printing and typesetting industry. Lorem Ipsum has been the industry's standard dummy text ever since the 1500s.</p>
  <span class="btn-blue">Read More</span>
</div>
<div class="abs feature f2">
  <div class="pic pic-cash" role="img" aria-label="Illustration of stacked banknotes"></div>
  <h3>Bill huge fees<br>every season</h3>
  <p>Lorem Ipsum is simply dummy text of the printing and typesetting industry. Lorem Ipsum has been the industry's standard dummy text ever since the 1500s.</p>
  <span class="btn-blue">Read More</span>
</div>
<div class="abs feature f3">
  <div class="pic pic-badge" role="img" aria-label="Money back guarantee seal"></div>
  <h3>Would rather<br>keep hidden</h3>
  <p>Lorem Ipsum is simply dummy text of the printing and typesetting industry. Lorem Ipsum has been the industry's standard dummy text ever since the 1500s.</p>
  <span class="btn-blue">Read More</span>
</div>

<div class="abs rule2"></div>

<h2 class="abs welcome">Welcome to Whispers from the Back Office!</h2>
<div class="abs video" role="img" aria-label="ClipNest promotional video of the author presenting the book">
  <svg width="84" height="46" viewBox="0 0 84 46"><rect x="0" y="0" width="84" height="46" rx="6" fill="rgba(255,255,255,.35)" stroke="rgba(255,255,255,.6)"/><path d="M35 12 L54 23 L35 34 Z" fill="rgba(90,90,90,.8)"/></svg>
</div>
<div class="abs body-copy">
  <p>Sed ut perspiciatis unde omnis iste natus error sit voluptatem accusantium doloremque laudantium,</p>
  <p>totam rem aperiam, eaque ipsa quae ab illo inventore veritatis et quasi architecto beatae vitae dicta sunt explicabo. Nemo enim ipsam voluptatem quia voluptas sit aspernatur aut odit aut fugit, sed quia consequuntur magni dolores eos qui ratione voluptatem sequi nesciunt.</p>
  <p>Neque porro quisquam est, qui dolorem ipsum quia dolor sit amet, consectetur, adipisci velit, sed quia non numquam eius modi tempora incidunt ut labore et dolore magnam aliquam quaerat voluptatem. Ut enim ad minima veniam, quis nostrum exercitationem ullam corporis suscipit laboriosam, ut labore et dolore magnam aliquam quaerat voluptatem. Ut enim ad minima veniam, quis nostrum exercitat</p>
</div>

<aside>
  <div class="abs side side-guarantee">
    <div class="seal" role="img" aria-label="100% money back guarantee seal"></div>
    <span class="label">Money Back Guarantee</span>
  </div>
  <div class="abs side side-buy">
    <div class="buy-btn">Buy Now</div>
    <div class="cards"><span>AmeriPass</span><span>Meridian</span><span>Vistra</span><span>Diskova</span></div>
  </div>
  <div class="abs side side-social">
    <div class="social-head"><span class="sq"></span><div><b>Friendloop Platform</b><span class="like">Like</span></div></div>
    <div class="social-count">1,988,819 people like Friendloop Platform.</div>
    <div class="fans">
      <div class="fan"><i role="img" aria-label="Member photo"></i>Dana</div>
      <div class="fan"><i role="img" aria-label="Member photo"></i>Mira</div>
      <div class="fan"><i role="img" aria-label="Member photo"></i>Theo</div>
      <div class="fan"><i role="img" aria-label="Member photo"></i>Kemal</div>
      <div class="fan"><i role="img" aria-label="Member photo"></i>Ruth</div>
    </div>
  </div>
</aside>

<footer class="abs footer"></footer>
<div class="abs copyright">Copyright 2013 © Whispers from the Back Office<span>|</span>Terms &amp; Conditions</div>
<div class="abs social-links">
  <span><i></i>Friendloop</span><span><i></i>Chirply</span><span><i></i>ClipNest</span><span><i></i>Coinvey</span><span><i></i>RSS</span>
</div>
</body>
</html>
```